Amber Reed Consulting Business Card

Hi Morwen. Thank you for your work on my coaching business card. I have another business which needs a new card. It is my counselling business. The best way to find out how to approach this project will be to go to my other website. www.amberreedconsulting.example.au and you will be able to see the colours scheme that I will require. White, Green and blue.

The tag line is Amber Reed Consulting So CALM STEPS TOWARD BRIGHTER DAYS. The clients are varied but mostly middle class Australian. The card is to show on it the same details as my other business card but with a different phone number. The tag lines are obviously different. The phone number is 5863 1427 The addresses are all the same.

Again simple, professional sophisticated is best.

Industry/Entity Type

Business

```html
<!DOCTYPE html>
<html lang="en">
<head>
<meta charset="utf-8">
<title>Amber Reed Consulting – Business Card</title>
<link href="https://fonts.googleapis.com/css2?family=Open+Sans:wght@400;600&display=swap" rel="stylesheet">
<style>
  :root {
    --stage: #e9e7e3;
    --blue-light: #3a68b4;
    --blue-dark: #1f3f86;
    --navy: #1d3a7a;
    --green: #8cc63f;
    --ink: #1b1b1b;
    --muted: #333333;
    --paper: #ffffff;
  }
  html, body { margin: 0; padding: 0; overflow: hidden; }
  body {
    width: 1200px; height: 757px;
    background: var(--stage);
    display: flex; align-items: center; justify-content: center; gap: 60px;
    font-family: "Open Sans", Arial, sans-serif;
  }
  .card {
    width: 520px; height: 318px; position: relative; box-sizing: border-box;
    box-shadow: 0 6px 18px rgba(0,0,0,.18);
  }
  /* Front */
  .card-front {
    background: linear-gradient(160deg, var(--blue-light), var(--blue-dark));
    color: #fff; display: flex; flex-direction: column; align-items: center; justify-content: center;
    text-align: center; padding: 0 30px;
  }
  .front-name {
    font-family: "Open Sans", Arial, sans-serif; font-weight: 400;
    font-size: 36px; letter-spacing: .3px; margin: 0;
  }
  .front-tagline { font-size: 14px; letter-spacing: 2.4px; margin: 12px 0 10px; }
  .front-services {
    color: var(--green); font-size: 12.5px; letter-spacing: 1.6px; font-weight: 600;
    line-height: 1.45; max-width: 400px; margin: 0;
  }
  /* Back */
  .card-back { background: var(--paper); color: var(--ink); }
  .back-brand { position: absolute; left: 26px; top: 96px; }
  .back-name {
    font-family: "Open Sans", Arial, sans-serif; font-weight: 400;
    color: var(--navy); font-size: 21px; margin: 0; line-height: 1.2;
  }
  .back-tagline { color: var(--green); font-size: 9.5px; letter-spacing: 1.6px; margin: 3px 0 0; }
  .person { position: absolute; right: 26px; top: 40px; text-align: right; }
  .person-name { font-size: 24px; margin: 0; line-height: 1.2; }
  .person-role { font-size: 10px; color: var(--muted); margin: 4px 0 0; }
  .divider { position: absolute; left: 0; right: 0; top: 152px; height: 2px; background: var(--green); }
  .contact-grid {
    position: absolute; left: 26px; right: 26px; top: 172px;
    display: grid; grid-template-columns: 1fr 1.4fr; gap: 4px 20px; font-size: 11px;
  }
  .contact-item { display: flex; align-items: center; gap: 7px; margin: 0; white-space: nowrap; }
  .contact-item svg { width: 11px; height: 11px; fill: var(--ink); flex: none; }
  .addresses { position: absolute; left: 26px; right: 20px; bottom: 24px; font-size: 10.5px; line-height: 1.55; margin: 0; }
</style>
</head>
<body>
  <section class="card card-front">
    <h1 class="front-name">Amber Reed Consulting</h1>
    <p class="front-tagline">CALM STEPS TOWARD BRIGHTER DAYS</p>
    <p class="front-services">ADVANCED COUNSELLING • COACHING • HYPNOTHERAPY AND PSYCHOTHERAPY</p>
  </section>

  <section class="card card-back">
    <div class="person">
      <p class="person-name">Tom Halloran</p>
      <p class="person-role">Clinical Psychotherapist and Executive Coach</p>
    </div>
    <div class="back-brand">
      <p class="back-name">Amber Reed Consulting</p>
      <p class="back-tagline">CALM STEPS TOWARD BRIGHTER DAYS</p>
    </div>
    <div class="divider"></div>
    <div class="contact-grid">
      <p class="contact-item"><svg viewBox="0 0 12 12"><path d="M2 1h2.5l1 3-1.5 1a7 7 0 0 0 3 3l1-1.5 3 1V10a1 1 0 0 1-1 1A9 9 0 0 1 1 2a1 1 0 0 1 1-1z"/></svg>+612 5863 1427</p>
      <p class="contact-item"><svg viewBox="0 0 12 12"><path d="M1 3h10v7H1z M2 4l4 3 4-3" fill="none" stroke="#1b1b1b"/></svg>tom@tomhalloran.example.au</p>
      <p class="contact-item"><svg viewBox="0 0 12 12"><path d="M3 1h6v3H3z M1 5h10v5H1z"/></svg>+612 5863 1429</p>
      <p class="contact-item"><svg viewBox="0 0 12 12"><circle cx="6" cy="6" r="5"/></svg>www.amberreedconsulting.example.au</p>
    </div>
    <p class="addresses">
      Glebe Office: 27 Wattle Lane Glebe NSW 2037<br>
      North Sydney Office: Suite 210 / 18 Alder Street North Sydney NSW 2060<br>
      Kestrel Street Office: Suite 502 / 90 Kestrel Street Sydney CBD NSW 2000
    </p>
  </section>
</body>
</html>
```